Business Card Design

We need a business card designed for our new company. Prefer a black card with white logo & writing.

Contact Information for Business Card

Ted Galloway, address: 7-4812 Fernhollow Road, Abbotsford, BC, V3K 8R2, Office Phone: 604-712-3390, Cell: 604-947-2164, Email: ted@resinworkshub.ca

Colors

Designer to choose only greyscale colors for use in the design.

```html
<!DOCTYPE html>
<html lang="en">
<head>
<meta charset="UTF-8">
<title>Resin Works Hub – Business Card</title>
<link href="https://fonts.googleapis.com/css2?family=Poppins:wght@300;400;700&display=swap" rel="stylesheet">
<style>
  :root {
    --canvas: #1f1f21;
    --card: #222225;
    --card-edge: #3a3a3e;
    --ink: #ffffff;
    --ink-soft: #e6e6e6;
  }
  * { margin: 0; padding: 0; box-sizing: border-box; }
  html, body {
    width: 1200px; height: 711px; overflow: hidden;
    background: var(--canvas);
    font-family: "Poppins", sans-serif;
    color: var(--ink);
  }
  .stage {
    position: relative; width: 1200px; height: 711px;
    display: flex; align-items: center; justify-content: center; gap: 40px;
  }
  .card {
    position: relative; width: 520px; height: 297px;
    background: var(--card);
    border-radius: 22px;
    border: 1px solid var(--card-edge);
    box-shadow: 0 14px 30px rgba(0,0,0,.55);
    overflow: hidden;
  }
  .brand {
    display: flex; align-items: center; gap: 12px;
    font-weight: 700; letter-spacing: .04em; text-transform: uppercase;
    color: var(--ink); line-height: 1;
  }
  .brand-mark {
    border: 3px solid var(--ink); border-radius: 50%; flex: none;
  }
  .card-front .brand {
    position: absolute; left: 50%; top: 50%; transform: translate(-50%, -50%);
    font-size: 34px; white-space: nowrap;
  }
  .card-front .brand-mark { width: 40px; height: 40px; }

  .card-back .brand {
    position: absolute; right: 30px; top: 30px; font-size: 19px; gap: 8px;
  }
  .card-back .brand-mark { width: 22px; height: 22px; border-width: 2px; }

  .contact {
    position: absolute; right: 30px; top: 104px;
    text-align: right; font-weight: 300; font-size: 12.5px; line-height: 1.45;
    color: var(--ink-soft);
  }
  .contact .address { margin-bottom: 10px; }
  .contact-line { display: flex; justify-content: flex-end; align-items: center; gap: 8px; }
  .contact-line svg { width: 12px; height: 12px; flex: none; }

  .person {
    position: absolute; left: 26px; bottom: 26px;
    transform-origin: left bottom;
    transform: translateX(48px) rotate(-90deg);
    white-space: nowrap;
  }
  .person-name { font-size: 24px; line-height: 1.1; }
  .person-name strong { font-weight: 700; }
  .person-name span { font-weight: 300; }
  .person-title { font-size: 12px; font-weight: 300; color: var(--ink-soft); }
</style>
</head>
<body>
<main class="stage">
  <section class="card card-front" aria-label="Card front">
    <div class="brand"><span class="brand-mark"></span>Resin Works Hub</div>
  </section>

  <section class="card card-back" aria-label="Card back">
    <div class="brand"><span class="brand-mark"></span>Resin Works Hub</div>

    <div class="contact">
      <p class="address">7-4812 Fernhollow Road,<br>Abbotsford, BC, V3K 8R2.</p>
      <p class="contact-line">604-712-3390
        <svg viewBox="0 0 24 24" fill="none" stroke="currentColor" stroke-width="2"><path d="M5 3h4l2 5-3 2a12 12 0 0 0 6 6l2-3 5 2v4a2 2 0 0 1-2 2A18 18 0 0 1 3 5a2 2 0 0 1 2-2z"/></svg>
      </p>
      <p class="contact-line">604-947-2164
        <svg viewBox="0 0 24 24" fill="none" stroke="currentColor" stroke-width="2"><rect x="6" y="2" width="12" height="20" rx="2"/><line x1="11" y1="18" x2="13" y2="18"/></svg>
      </p>
      <p class="contact-line">www.resinworkshub.ca
        <svg viewBox="0 0 24 24" fill="none" stroke="currentColor" stroke-width="2"><circle cx="12" cy="12" r="10"/><path d="M2 12h20M12 2a15 15 0 0 1 0 20M12 2a15 15 0 0 0 0 20"/></svg>
      </p>
      <p class="contact-line">ted@resinworkshub.ca
        <svg viewBox="0 0 24 24" fill="none" stroke="currentColor" stroke-width="2"><rect x="2" y="5" width="20" height="14" rx="1"/><path d="M2 6l10 7 10-7"/></svg>
      </p>
    </div>

    <div class="person">
      <p class="person-name"><strong>Ted</strong> <span>Galloway</span></p>
      <p class="person-title">Founder &amp; CEO</p>
    </div>
  </section>
</main>
</body>
</html>
```